Carmen Poster

We need a poster for the upcoming production of Opera Carmen. We want a modern looking avant garde poster with some traditional ellemnts. opera will be stage "out of the period" which means that there will be NO indication of time period or location. Colors for the set design are white and dark burgundy. some traditional Spanish elements will be used, particularly in the female costumes.

Target Market(s)

Arts community in Hartford and central CT

Requirements
Must have
• Logos of opera and orchestra.
• BIZET CARMEN
• Carmen:
• Lorna Beth Whitfield
• Don José:
• Nathaniel Dorsett
• Escamillo:
• Morgan Piel
• Micaëla:
• Anneliese Vorck,
• Ruth Halpin
• Stage Director, Conductor
• Tobias Warnick
• Chorus Master
• Lena Fairgrove
• www.brambleoperahouse.org
• www.quillensemble.org
• (860) 472-8196
• Fri. November 9 / 7:30 pm / New Britain
• Alderhall-By-Pond (47 Birch St)
• Sun. November 11 / 4 pm / New London
• Velm Arts Center (518 Cedar St)
• Sat. November 17 / 7:30 / Middletown
• KWT Performing Arts Center (300 Tern Cove Ln)
• Sun. November 18 / 2 pm / Hartford
• Pembrook Gallery Museum of Art (800 Birch St)
Should not have
• NOTE. Please see the graphics as suggestions. you an use other , you don't have to use all the graphics.

```html
<!DOCTYPE html>
<html lang="en">
<head>
<meta charset="utf-8">
<title>Carmen – Bramble Opera House</title>
<link rel="stylesheet" href="https://fonts.googleapis.com/css2?family=Poppins:ital,wght@0,400;0,500;0,700;1,400&display=swap">
<style>
  :root {
    --burgundy: #5c0a2c;
    --burgundy-deep: #4a0e1f;
    --teal: #2e8f8d;
    --gold: #d9b43a;
    --title-gold: #e4be3b;
    --brick-a: #b25a3c;
    --brick-b: #7a3a2a;
    --figure-top: #5a5557;
    --figure-mid: #8a4a55;
    --figure-bottom: #d9505e;
    --white: #ffffff;
    --logo-blue: #1d2aa8;
    --ink: #111111;
  }
  * { box-sizing: border-box; margin: 0; padding: 0; }
  html, body { width: 776px; height: 1200px; overflow: hidden; background: var(--burgundy); }
  .poster {
    position: relative; width: 776px; height: 1200px; overflow: hidden;
    background: var(--burgundy);
    font-family: "Poppins", Arial, sans-serif; color: var(--white);
  }
  .backdrop { position: absolute; inset: 0; }
  .logo {
    position: absolute; background: var(--white);
    display: flex; align-items: center; text-align: center;
  }
  .logo--orchestra {
    left: 44px; top: 34px; width: 226px; height: 56px;
    color: var(--logo-blue); font-weight: 700; font-size: 17px; line-height: 17px;
    text-transform: uppercase; justify-content: flex-start; padding-left: 6px; text-align: left;
  }
  .logo--opera {
    left: 82px; top: 102px; width: 149px; height: 92px; justify-content: center;
    color: var(--ink); font-weight: 500; font-size: 15px; line-height: 18px; text-transform: uppercase;
  }
  .title {
    position: absolute; left: 354px; top: 21px;
    font-family: "Poppins", Arial, sans-serif; font-weight: 700;
    font-size: 162px; line-height: 140px; color: var(--title-gold); letter-spacing: -1px;
  }
  .schedule { position: absolute; left: 71px; top: 296px; width: 340px; }
  .performance { margin-bottom: 16px; }
  .performance__day { font-weight: 700; font-size: 23px; line-height: 30px; }
  .performance__time { font-size: 19px; line-height: 26px; }
  .performance__venue { font-size: 18px; line-height: 24px; }
  .performance:first-child .performance__time { font-size: 23px; line-height: 30px; }
  .performance:first-child .performance__venue { line-height: 26px; }
  .credits { position: absolute; left: 71px; top: 776px; font-size: 18px; line-height: 25.5px; }
  .credits__role { font-style: italic; }
  .credits__line { white-space: nowrap; }
  .credits__gap { height: 13px; }
  .footer {
    position: absolute; left: 0; bottom: 0; width: 776px; height: 80px;
    background: var(--burgundy-deep); text-align: center;
    font-size: 19px; line-height: 27px; padding-top: 11px; letter-spacing: 0.3px;
  }
  .footer__phone { display: inline-flex; align-items: center; gap: 8px; }
</style>
</head>
<body>
<main class="poster">
  <svg class="backdrop" width="776" height="1200" viewBox="0 0 776 1200">
    <defs>
      <linearGradient id="brickTone" x1="0" y1="0" x2="1" y2="1">
        <stop offset="0" stop-color="var(--brick-a)"/>
        <stop offset="1" stop-color="var(--brick-b)"/>
      </linearGradient>
      <linearGradient id="figureTone" x1="0" y1="0" x2="0" y2="1">
        <stop offset="0" stop-color="var(--figure-top)"/>
        <stop offset="0.55" stop-color="var(--figure-mid)"/>
        <stop offset="1" stop-color="var(--figure-bottom)"/>
      </linearGradient>
    </defs>
    <polygon class="panel-teal" points="385,0 776,780 776,1120 330,1120 0,590" fill="var(--teal)"/>
    <polygon class="panel-gold" points="0,590 330,1120 0,1120" fill="var(--gold)"/>
    <polygon class="panel-brick" points="385,0 776,0 776,780" fill="url(#brickTone)" role="img" aria-label="Photograph of an old red brick wall"/>
    <rect class="figure-area" x="400" y="380" width="376" height="740" fill="url(#figureTone)" opacity="0.92" role="img" aria-label="Illustration of a woman with a red flower in her hair, a silver hoop earring and an open red fan"/>
  </svg>

  <div class="logo logo--orchestra">Quill Chamber<br>Ensemble</div>
  <div class="logo logo--opera">Bramble<br>Opera House</div>

  <h1 class="title">CaR<br>MeN</h1>

  <section class="schedule">
    <div class="performance">
      <div class="performance__day">Friday | November 9</div>
      <div class="performance__time">7:30 PM &nbsp;| New Britain</div>
      <div class="performance__venue">Alderhall-By-Pond (47 Birch St)</div>
    </div>
    <div class="performance">
      <div class="performance__day">Sunday | November 11</div>
      <div class="performance__time">4 pm | New London</div>
      <div class="performance__venue">Velm Arts Center (518 Cedar St)</div>
    </div>
    <div class="performance">
      <div class="performance__day">Saturday | November 17</div>
      <div class="performance__time">7:30 &nbsp;| Middletown</div>
      <div class="performance__venue">KWT Performing Arts Center<br>(300 Tern Cove Ln)</div>
    </div>
    <div class="performance">
      <div class="performance__day">Sunday | November 18</div>
      <div class="performance__time">2 pm | Hartford</div>
      <div class="performance__venue">Pembrook Gallery<br>Museum of Art (800 Birch St)</div>
    </div>
  </section>

  <section class="credits">
    <div class="credits__line"><span class="credits__role">Carmen</span>: &nbsp;&nbsp;Lorna Beth Whitfield</div>
    <div class="credits__line"><span class="credits__role">Don José</span>: &nbsp;Nathaniel Dorsett</div>
    <div class="credits__line"><span class="credits__role">Escamillo</span>: &nbsp;Morgan Piel</div>
    <div class="credits__line"><span class="credits__role">Micaëla</span>: &nbsp;Anneliese Vorck, Ruth Halpin</div>
    <div class="credits__gap"></div>
    <div class="credits__line"><span class="credits__role">Stage Director, Conductor</span></div>
    <div class="credits__line">Tobias Warnick</div>
    <div class="credits__line">Chorus Master</div>
    <div class="credits__line">Lena Fairgrove</div>
  </section>

  <footer class="footer">
    <div>www.brambleoperahouse.org | www.quillensemble.org</div>
    <div class="footer__phone">
      <svg width="16" height="16" viewBox="0 0 24 24" aria-hidden="true"><circle cx="12" cy="12" r="11" fill="none" stroke="#fff" stroke-width="1.6"/><path d="M9 6 l2 3 -1.5 1.5 q1 2.5 3.5 4 l1.5 -1.5 3 2 -1.5 2.5 q-5 0 -8.5 -5.5 q-1.5 -3 0.5 -6 z" fill="#fff"/></svg>
      (860) 472-8196
    </div>
  </footer>
</main>
</body>
</html>
```